Professional Services - letterhead / business cards

The company (velmora partners) will provide services to Investment Funds and large investors in Spain. I have recently chosen a logo that I am attaching.

I would like a simple stationary design that i could use as letter head, business cards and "with compliments" cards.

I am not quite sure which color I will mostly use for the logo, in the email signature I will probably lean towards the white background and grey letters. I am attaching my favourite options.

Target Market(s)

Large Multinationals, Investment funds and Law firms

Industry/Entity Type

Business

Requirements
Must have
• my details are:
Luis R. Abadal
Velmora Partners S.L.
Casa de Torrelumbre
Calle de Vientoalto 27
28014 Madrid
T: +34 (91) 387-2265
M: +34 (646) 819-054
e-mail: labadal@velmorapartners.com

```html
<!DOCTYPE html>
<html lang="en">
<head>
<meta charset="utf-8">
<title>Velmora Partners – Business Card</title>
<link rel="stylesheet" href="https://fonts.googleapis.com/css2?family=Questrial&display=swap">
<style>
  :root {
    --navy: #13137a;
    --navy-deep: #0d0d63;
    --silver: #b4b6bb;
    --paper: #ffffff;
    --ink-soft: #6d6f78;
    --backdrop: #e9e7e3;
  }
  * { box-sizing: border-box; margin: 0; padding: 0; }
  html, body {
    width: 1200px; height: 588px; overflow: hidden;
    background: var(--backdrop);
    font-family: "Questrial", "Century Gothic", sans-serif;
  }
  .stage {
    width: 1200px; height: 588px;
    display: flex; align-items: center; justify-content: center; gap: 40px;
  }
  .card {
    position: relative;
    width: 520px; height: 300px;
    border-radius: 16px;
    overflow: hidden;
    box-shadow: 0 6px 18px rgba(0,0,0,.18);
  }

  /* Back side */
  .card--back {
    background: var(--navy);
    color: var(--paper);
    display: flex; flex-direction: column; align-items: center; justify-content: center;
  }
  .card--back .wordmark { font-size: 44px; letter-spacing: .5px; }
  .card--back .website {
    margin-top: 22px; font-size: 14px; letter-spacing: 3px;
  }

  /* Front side */
  .card--front { background: var(--paper); }
  .card__wave { position: absolute; inset: 0; width: 100%; height: 100%; }
  .card--front .wordmark {
    position: absolute; top: 34px; left: 0; width: 100%;
    text-align: center; padding-left: 120px;
    font-size: 34px; color: var(--navy);
  }
  .holder {
    position: absolute; top: 96px; left: 0; width: 100%;
    text-align: center; padding-left: 120px;
  }
  .holder__name { font-size: 17px; letter-spacing: 1.5px; color: var(--navy); text-transform: uppercase; }
  .holder__company { font-size: 11px; color: var(--ink-soft); margin-top: 2px; }
  .holder__email { font-size: 12px; color: var(--ink-soft); margin-top: 2px; }
  .holder__email b { font-weight: 400; color: var(--navy); }

  .contact {
    position: absolute; left: 0; width: 100%;
    color: var(--paper); font-size: 13px;
  }
  .contact--phones {
    top: 200px; display: flex; gap: 22px; justify-content: center; padding-left: 40px;
  }
  .phone { display: flex; align-items: center; gap: 7px; }
  .phone__badge {
    width: 16px; height: 16px; border-radius: 50%;
    background: var(--silver); color: var(--paper);
    font-size: 9px; display: flex; align-items: center; justify-content: center;
  }
  .contact--address { top: 248px; text-align: center; font-size: 12.5px; }
</style>
</head>
<body>
  <main class="stage">
    <section class="card card--back" aria-label="Business card, back">
      <div class="wordmark">velmora partners</div>
      <div class="website">www.velmorapartners.com</div>
    </section>

    <section class="card card--front" aria-label="Business card, front">
      <svg class="card__wave" viewBox="0 0 520 300" preserveAspectRatio="none" aria-hidden="true">
        <path d="M0 118 C130 98 270 150 520 232 L520 252 C270 176 130 132 0 146 Z" fill="var(--silver)"/>
        <path d="M0 146 C130 132 270 176 520 252 L520 300 L0 300 Z" fill="var(--navy)"/>
        <path d="M0 158 C140 144 280 190 520 266 L520 300 L0 300 Z" fill="var(--navy-deep)" opacity=".35"/>
      </svg>

      <div class="wordmark">velmora partners</div>

      <div class="holder">
        <div class="holder__name">Luis R. Abadal</div>
        <div class="holder__company">Velmora Partners S.L.</div>
        <div class="holder__email">labadal@<b>velmorapartners</b>.com</div>
      </div>

      <div class="contact contact--phones">
        <span class="phone"><span class="phone__badge">P</span>+34 (91) 387-2265</span>
        <span class="phone"><span class="phone__badge">C</span>+34 (646) 819-054</span>
      </div>
      <div class="contact contact--address">Casa de Torrelumbre, Calle de Vientoalto 27, 28014 Madrid</div>
    </section>
  </main>
</body>
</html>
```